Redesign of LumoWordfind.com in Bootstrap 4

Current design of LumoWordfind.com is not responsive. We need to change it to latest version of Bootstrap 4 keeping essential elements in place.

Apart from home page, we need designs for http://www.lumowordfind.com/meaning/cat also.

Coding

Number of Pages Required

2 page

Colors
34a7d8

Requirements
Must have
• Bootstrap 4

```html
<!DOCTYPE html>
<html lang="en">
<head>
<meta charset="utf-8">
<title>Lumo Wordfind – Home</title>
<link href="https://fonts.googleapis.com/css2?family=Open+Sans:wght@400;600;700&display=swap" rel="stylesheet">
<style>
:root{
  --brand:#34a7d8;
  --brand-dark:#1f7fb4;
  --accent:#f39a1d;
  --ink:#333;
  --muted:#888;
  --line:#dcdcdc;
  --navy:#1d3f66;
  --blue-band:#3f94c6;
  --slate-band:#2e3a44;
  --grid-band:#3a9ad2;
  --addon-band:#3b4147;
  --footer:#2a2a2a;
  --white:#fff;
}
*{box-sizing:border-box;margin:0;padding:0}
html,body{width:744px;height:1200px;overflow:hidden}
body{font-family:'Open Sans',sans-serif;color:var(--ink);background:var(--white);position:relative}
a{color:inherit;text-decoration:none}

.site-header{height:62px;border-top:2px solid var(--accent);position:relative;border-bottom:1px solid #eee}
.brand{position:absolute;left:62px;top:22px;display:flex;align-items:center;gap:5px;font-weight:700;font-size:12px;color:var(--navy);line-height:1}
.brand-dot{width:10px;height:10px;border-radius:50%;background:var(--accent)}
.main-nav{position:absolute;left:199px;top:23px;font-size:7.5px;text-transform:uppercase;color:#333}
.main-nav a{position:absolute;white-space:nowrap}
.btn-login{position:absolute;right:62px;top:16px;width:58px;height:22px;background:var(--brand);color:var(--white);font-size:9px;font-weight:600;display:flex;align-items:center;justify-content:center;border-radius:2px}

.wotd{height:40px;position:relative;background:#fafafa;border-bottom:1px solid #eee}
.wotd-label{position:absolute;left:0;top:0;width:190px;height:40px;background:var(--white);color:var(--brand-dark);font-size:13px;padding:12px 0 0 62px;clip-path:polygon(0 0,180px 0,190px 50%,180px 100%,0 100%)}
.wotd-word{position:absolute;left:217px;top:12px;font-size:12.5px;font-weight:600;color:#444}
.wotd-word span{font-weight:400;color:var(--muted);font-size:10.5px}
.wotd-link{position:absolute;left:508px;top:15px;font-size:8.5px;font-style:italic;color:var(--brand-dark);text-decoration:underline;font-family:Georgia,serif}
.btn-search{position:absolute;right:62px;top:9px;width:80px;height:22px;background:var(--brand);color:var(--white);font-size:8.5px;font-weight:600;display:flex;align-items:center;justify-content:center}

.hero{position:absolute;left:0;top:102px;width:744px;height:319px;color:var(--white);overflow:hidden}
.hero-photo{position:absolute;inset:0;background:linear-gradient(100deg,#b3461f 0%,#d6792e 18%,#8d6a4a 32%,#7c8a8a 55%,#9aa6a4 78%,#b9bdb6 100%)}
.hero-mark{position:absolute;right:70px;top:38px;font-size:30px;font-weight:700;color:rgba(255,255,255,.25);line-height:1}
.hero-title{position:absolute;right:70px;top:110px;font-size:19px;font-weight:600;letter-spacing:-.2px;text-shadow:0 1px 2px rgba(0,0,0,.3)}
.hero-list{position:absolute;right:70px;top:150px;list-style:none;text-align:right;font-size:11px}
.hero-list li{height:33px;display:flex;justify-content:flex-end;align-items:flex-start;gap:10px}
.hero-list svg{width:9px;height:9px;margin-top:3px}
.hero-arrow{position:absolute;top:214px;width:10px;height:14px}

.browse{position:absolute;left:62px;top:452px;display:flex;gap:4px;font-size:10.5px}
.browse-label{width:86px;height:21px;border:1px solid var(--line);color:var(--brand-dark);font-size:8.5px;display:flex;align-items:center;justify-content:center;margin-right:9px}
.browse a{width:16px;height:21px;border:1px solid var(--line);display:flex;align-items:center;justify-content:center;color:#555}
.browse a.active{color:var(--brand)}

.feature{position:absolute;left:0;width:744px;color:var(--white);overflow:hidden}
.feature h2{font-size:14px;font-weight:400;text-transform:uppercase;position:absolute;white-space:nowrap}
.feature p{font-size:10.5px;line-height:18px;position:absolute}
.feature .more{font-size:7.5px;text-transform:uppercase;position:absolute;white-space:nowrap}
.feature .art{position:absolute;border:1px solid rgba(255,255,255,.7)}

.f-phone{top:501px;height:155px;background:var(--blue-band)}
.f-phone .art{left:92px;top:8px;width:230px;height:140px;border:0;background:linear-gradient(135deg,#cfd6db,#f3f3f3 40%,#a9b0b4);border-radius:18px;transform:rotate(26deg) scale(.75)}
.f-phone h2{right:70px;top:46px}
.f-phone p{right:70px;top:66px;font-size:8.5px;line-height:15px;text-align:right;width:300px}
.f-phone .more{right:76px;top:105px}

.f-tidbit{top:656px;height:156px;background:var(--slate-band)}
.f-tidbit h2{right:358px;top:19px;font-size:15px}
.f-tidbit .sub{position:absolute;right:360px;top:47px;font-size:7.5px}
.f-tidbit p{right:358px;top:69px;width:330px;text-align:right;font-size:10.5px}
.f-tidbit .more{right:360px;top:120px}
.f-tidbit .art{left:454px;top:21px;width:229px;height:114px;background:linear-gradient(135deg,#6d8fae,#cfdbe6 45%,#3b5a78)}

.f-cross{top:812px;height:155px;background:var(--grid-band)}
.f-cross .art{left:62px;top:21px;width:228px;height:113px;background:linear-gradient(120deg,#e7c6b4,#f4e7df 50%,#bfc3cc)}
.f-cross h2{right:70px;top:42px;font-size:15px}
.f-cross p{right:70px;top:70px;font-size:10.5px}
.f-cross .more{right:75px;top:96px;font-size:9px}

.f-addon{top:967px;height:156px;background:var(--addon-band)}
.f-addon h2{right:358px;top:31px;font-size:15px}
.f-addon p{right:358px;top:62px;width:330px;text-align:right;font-size:10.5px}
.f-addon .more{right:360px;top:118px}
.f-addon .art{left:454px;top:22px;width:229px;height:112px;background:radial-gradient(circle at 30% 45%,#f4f4f4 0,#dfe4e8 40%,#8b959d 100%)}

.site-footer{position:absolute;left:0;top:1123px;width:744px;height:77px;background:var(--footer);color:#ddd}
.footer-brand{position:absolute;left:84px;top:30px;font-size:11px;font-weight:700;color:var(--accent);display:flex;align-items:center;gap:5px}
.footer-brand i{width:8px;height:8px;background:var(--brand);display:block}
.divider{position:absolute;top:18px;width:1px;height:42px;background:#444}
.social{position:absolute;left:288px;top:27px;display:flex;gap:13px}
.social span{width:23px;height:23px;border-radius:2px}
.legal{position:absolute;right:70px;top:28px;font-size:7.5px;text-align:right;line-height:15px}
.code{position:absolute;right:18px;top:58px;font-size:7.5px}
</style>
</head>
<body>
<header class="site-header">
  <a class="brand" href="#"><span class="brand-dot"></span>Lumo Wordfind</a>
  <nav class="main-nav">
    <a style="left:0">Home</a><a style="left:59px">Idioms</a><a style="left:123px">Common Errors</a><a style="left:226px">Crossword</a><a style="left:309px">Blog</a><a style="left:366px">Contact</a>
  </nav>
  <a class="btn-login" href="#">LOG IN</a>
</header>

<section class="wotd">
  <div class="wotd-label">Word Of The Day</div>
  <div class="wotd-word">EXHAUSTIVE - <span>considering all elements or aspects</span></div>
  <a class="wotd-link" href="#">Show full Definition</a>
  <a class="btn-search" href="#">SEARCH HERE</a>
</section>

<section class="hero">
  <div class="hero-photo" role="img" aria-label="Stack of old books on a wooden table"></div>
  <div class="hero-mark">Lumo Wordfind</div>
  <h1 class="hero-title">SEARCH, SAVE AND MASTER WORDS</h1>
  <ul class="hero-list">
    <li>Search from more than 300,000 words and phrases<svg viewBox="0 0 10 10"><path d="M1 5l3 3 5-7" stroke="#fff" stroke-width="2" fill="none"/></svg></li>
    <li>Multiple usages to clarify the context<svg viewBox="0 0 10 10"><path d="M1 5l3 3 5-7" stroke="#fff" stroke-width="2" fill="none"/></svg></li>
    <li>Audio, phonetics, meanings, synonyms and antonyms<svg viewBox="0 0 10 10"><path d="M1 5l3 3 5-7" stroke="#fff" stroke-width="2" fill="none"/></svg></li>
    <li>Save the words to your personal deck and access from anywhere<svg viewBox="0 0 10 10"><path d="M1 5l3 3 5-7" stroke="#fff" stroke-width="2" fill="none"/></svg></li>
    <li>It's FREE<svg viewBox="0 0 10 10"><path d="M1 5l3 3 5-7" stroke="#fff" stroke-width="2" fill="none"/></svg></li>
  </ul>
  <svg class="hero-arrow" style="left:27px" viewBox="0 0 10 14"><path d="M8 1L2 7l6 6" stroke="#fff" stroke-width="2" fill="none"/></svg>
  <svg class="hero-arrow" style="left:705px" viewBox="0 0 10 14"><path d="M2 1l6 6-6 6" stroke="#fff" stroke-width="2" fill="none"/></svg>
</section>

<nav class="browse">
  <span class="browse-label">Browse Dictionary</span>
  <a class="active">A</a><a>B</a><a>C</a><a>D</a><a>E</a><a>F</a><a>G</a><a>H</a><a>I</a><a>J</a><a>K</a><a>L</a><a>M</a><a>N</a><a>O</a><a>P</a><a>Q</a><a>R</a><a>S</a><a>T</a><a>U</a><a>V</a><a>W</a><a>X</a><a>Y</a><a>Z</a>
</nav>

<section class="feature f-phone">
  <div class="art" role="img" aria-label="Smartphone showing a dictionary page"></div>
  <h2>Designed for Nimbus Phone</h2>
  <p>Lumo Wordfind is specially designed for your Nimbus Phone to quickly lookup meaining, usages and audio of words.</p>
  <a class="more">Read more &gt;&gt;</a>
</section>

<section class="feature f-tidbit">
  <h2>English Tidbit</h2>
  <span class="sub">gaffe / gaff</span>
  <p>"Gaffe" is a social blunder and "gaff" is a large hook. Be warned not to make the gaffe of mixing it up with gaff.</p>
  <a class="more">Read more &gt;&gt;</a>
  <div class="art" role="img" aria-label="Glass roof with an information sign"></div>
</section>

<section class="feature f-cross">
  <div class="art" role="img" aria-label="Hands filling in a crossword with a pencil"></div>
  <h2>Crossword Lovers!</h2>
  <p>Take this daily crossword challenge from Lumo Wordfind.</p>
  <a class="more">Solve now !!!</a>
</section>

<section class="feature f-addon">
  <h2>Kestrel Browser Addon</h2>
  <p>Add this tool to your Kestrel Browser and quickly look up for definitions from any website without leaving the page.</p>
  <a class="more">Get it now !!</a>
  <div class="art" role="img" aria-label="Browser window seen through a magnifying glass"></div>
</section>

<footer class="site-footer">
  <div class="footer-brand"><i></i>Lumo Wordfind</div>
  <span class="divider" style="left:216px"></span>
  <div class="social" aria-label="Social links">
    <span style="background:#3b5998"></span><span style="background:#1da1f2"></span><span style="background:#4a6ea9"></span><span style="background:#d34836"></span>
  </div>
  <span class="divider" style="left:490px"></span>
  <div class="legal">All Rights Reserved . Privacy Policy<br>copyrights2016@companyname.com</div>
  <div class="code">C18</div>
</footer>
</body>
</html>
```